Refresh of far from plain IT company website

Our web site is starting to show it's age. You can see the existing site here: www.plumbwick.net. As a growing company we want to come across as a dynamic collection of IT experts.

We want to update the design so are open to any colour palette and look, but want to retain our current table logo. We use the logo on our business cards but with a white background - see the attached file, so you don't need to keep the brown or the green.

The design should consider the range of browsers that will be looking at the site - so please show how it will look on a wide screen laptop and a 768x1024 tablet.

We want to add some pages about our team and their skills, probably with photos of each person on the team.

This is an uncoded project - the PSD files of the design is required, not coding.
Updates

Thanks everyone for the submissions so far.  It's a holiday day in the UK today but we will get some feedback on the designs so far out to you.

Target Market(s)

Architects and other creative types looking for IT support

Industry/Entity Type

Business

Font styles to use
Serif
Sans Serif

Requirements
Must have
• Must look good on a laptop and an iPad.

```html
<!DOCTYPE html>
<html lang="en">
<head>
<meta charset="utf-8">
<title>plumbwick — Serious IT support for business</title>
<link rel="stylesheet" href="https://fonts.googleapis.com/css2?family=Ubuntu:wght@400;500;700&family=Dancing+Script:wght@700&display=swap">
<style>
:root{
  --maroon:#980a52;
  --gold:#dcaa00;
  --gold-light:#f0cf4a;
  --ink:#333;
  --grey-text:#666;
  --nav-dark:#4a4a4a;
  --hero-deep:#0b4f8f;
  --hero-mid:#1d86c9;
  --hero-light:#6fd0f2;
  --white:#fff;
}
*{box-sizing:border-box;margin:0;padding:0}
html,body{width:1043px;height:1200px;overflow:hidden;background:var(--white);font-family:"Ubuntu",sans-serif;color:var(--ink)}
.page{position:relative;width:1043px;height:1200px;overflow:hidden}
.abs{position:absolute}
.top-rule{left:0;top:0;width:1043px;height:4px;background:var(--gold)}
.live-chat{left:815px;top:4px;width:114px;height:20px;background:var(--gold);color:var(--maroon);font-size:12px;font-weight:500;display:flex;align-items:center;justify-content:center;gap:6px}
.brand{left:114px;top:22px;display:flex;align-items:center;gap:16px}
.brand-mark{width:58px;height:50px;background:var(--gold)}
.brand-name{font-size:49px;font-weight:500;color:var(--maroon);letter-spacing:-0.5px;line-height:1}
.call{left:758px;top:46px;display:flex;gap:8px;align-items:center}
.call-label{font-size:11px;color:var(--gold);font-weight:500;margin-left:4px}
.call-number{font-size:21px;color:var(--maroon);line-height:1.1}
.nav{left:114px;top:108px;width:815px;height:27px;display:flex;background:linear-gradient(#5c5c5c,#3d3d3d);border-radius:3px 3px 0 0;overflow:hidden}
.nav a{display:flex;align-items:center;justify-content:center;color:#fff;font-size:11.5px;font-weight:500;text-decoration:none;border-left:1px solid #2d2d2d;letter-spacing:.3px}
.nav a.active{background:var(--gold);color:var(--maroon);border-left:none}
.hero{left:0;top:135px;width:1043px;height:398px;background:radial-gradient(circle at 47% 50%,var(--hero-light) 0%,var(--hero-mid) 35%,var(--hero-deep) 100%)}
.hero-script{left:114px;top:172px;font-family:"Dancing Script",cursive;font-size:36px;color:#fff;text-shadow:0 2px 3px rgba(0,0,0,.4)}
.hero-title{left:117px;top:228px;font-size:24px;font-weight:500;color:#fff;text-shadow:0 1px 2px rgba(0,0,0,.4)}
.hero-lines{left:117px;top:268px;font-size:15px;line-height:21.5px;color:#fff}
.btn-read{left:114px;top:353px;width:172px;height:44px;border-radius:4px;background:linear-gradient(var(--gold-light),var(--gold));color:#fff;font-size:19px;font-weight:700;display:flex;align-items:center;justify-content:center;text-shadow:0 1px 2px rgba(0,0,0,.35);box-shadow:0 3px 5px rgba(0,0,0,.3)}
.slide-arrow{top:294px;width:40px;height:40px;border-radius:50%;background:#222;border:2px solid #555;display:flex;align-items:center;justify-content:center}
.below-hero{left:0;top:533px;width:1043px;height:70px;background:linear-gradient(#e4e4e4,#fff)}
.services{left:114px;top:444px;width:815px;height:130px;background:#fff;border:1px solid #ddd}
.services-tab{left:444px;top:428px;width:155px;height:32px;background:linear-gradient(#fff,#e8e8e8);border-radius:5px 5px 0 0;font-size:19px;font-weight:500;color:#444;display:flex;align-items:center;justify-content:center}
.service{top:470px;width:170px;text-align:center;font-size:12px;font-weight:500;color:#333}
.service-icon{width:50px;height:50px;border-radius:50%;background:var(--gold);margin:0 auto 16px;display:flex;align-items:center;justify-content:center;box-shadow:0 3px 3px rgba(0,0,0,.2)}
.service-sep{top:465px;width:1px;height:105px;background:linear-gradient(#fff,#e5e5e5,#fff)}
.welcome-mark{left:117px;top:597px;width:40px;height:36px;background:var(--gold)}
.welcome-title{left:189px;top:606px;font-size:17px;font-weight:500}
.welcome-title span{color:var(--maroon);font-size:23px}
.dots{left:114px;top:648px;width:518px;border-top:1px dotted #888}
.about-text{left:115px;top:654px;width:516px;font-size:11.4px;line-height:16.5px;color:var(--grey-text);text-align:justify;letter-spacing:.2px}
.about-text p+p{margin-top:7px}
.read-more{left:556px;top:766px;font-size:12px;font-weight:700;color:var(--maroon)}
.video{left:654px;top:610px;width:275px;height:163px;background:#eee;box-shadow:0 4px 6px rgba(0,0,0,.25)}
.video-frame{width:275px;height:148px;background:linear-gradient(135deg,#3a3a3a,#b9b2a8 45%,#5d544c)}
.video-bar{width:275px;height:15px;background:linear-gradient(#f4f4f4,#cfcfcf);display:flex;align-items:center;gap:5px;padding:0 5px;font-size:6px;color:#333}
.track{flex:1;height:3px;background:#999;border-radius:2px}
.rule{left:122px;top:811px;width:800px;height:6px;background:radial-gradient(ellipse at center,#ddd,rgba(255,255,255,0) 70%)}
.news{left:114px;top:834px;width:815px;height:50px;border:1px solid #ddd;border-radius:3px;background:linear-gradient(#fff,#eaeaea)}
.date{left:126px;top:842px;width:36px;height:37px;background:var(--maroon);color:#fff;text-align:center}
.date .m{background:var(--gold);font-size:10px;font-weight:700;height:14px;line-height:14px}
.date .d{font-size:15px;font-weight:700;line-height:22px}
.news-text{left:207px;top:840px;width:712px;font-size:11.4px;line-height:17px;color:var(--grey-text)}
.news-text b{color:#555;font-weight:500}
.view-all{left:853px;top:865px;font-size:11.5px;font-weight:700;color:var(--maroon)}
.footer{left:0;top:914px;width:1043px;height:245px;background:var(--maroon);color:#fff}
.foot-h{font-size:16px;color:#fff}
.foot-link{font-size:10.5px;color:#fff;letter-spacing:.3px}
.foot-link::before{content:"›";color:var(--gold);margin-right:10px;font-size:12px}
.divider{top:937px;width:1px;height:131px;background:rgba(255,255,255,.25)}
.field{left:346px;width:207px;background:#fff;border:1px solid #d8b;border-radius:3px;font-size:9.5px;color:#999;padding:3px 12px}
.btn-gold{background:var(--gold);color:#fff;font-size:12px;font-weight:700;border-radius:3px;display:flex;align-items:center;justify-content:center}
.info{left:601px;display:flex;gap:10px;font-size:11px;line-height:13.5px;color:#fff}
.info svg{flex:none}
.social{top:1113px;width:23px;height:23px;border-radius:3px}
.copyright{left:0;top:1159px;width:1043px;height:41px;background:var(--gold);color:#333;font-size:13px;display:flex;align-items:center;justify-content:center}
</style>
</head>
<body>
<div class="page">
  <div class="abs top-rule"></div>
  <div class="abs live-chat">
    <svg width="16" height="13" viewBox="0 0 16 13"><ellipse cx="7" cy="5.5" rx="6.5" ry="4.5" fill="none" stroke="#980a52" stroke-width="1.6"/><path d="M3 9 L2 12 L6 9.8" fill="#980a52"/></svg>
    LIVE CHAT
  </div>

  <div class="abs brand"><div class="brand-mark"></div><div class="brand-name">plumbwick</div></div>

  <div class="abs call">
    <svg width="18" height="34" viewBox="0 0 18 34"><path d="M12 2 C4 4 2 12 3 18 C4 26 8 31 13 32 L15 27 C11 26 9 21 9 17 C9 12 10 8 14 7 Z" fill="#111"/></svg>
    <div><div class="call-label">Call Us</div><div class="call-number">020 7946 0321</div></div>
  </div>

  <nav class="abs nav">
    <a class="active" style="width:84px">HOME</a>
    <a style="width:100px">ABOUT US</a>
    <a style="width:120px">WHAT WE DO</a>
    <a style="width:112px">NEWS BLOG</a>
    <a style="width:95px">ARTICLES</a>
    <a style="width:89px">CLIENTS</a>
    <a style="width:103px">PARTNERS</a>
    <a style="width:112px">CONTACT US</a>
  </nav>

  <div class="abs hero" role="img" aria-label="Photo of a finger touching a glowing blue touchscreen"></div>
  <div class="abs hero-script">Serious IT support for business</div>
  <div class="abs hero-title">Lorem ipsum dolor sit amet</div>
  <div class="abs hero-lines">Lorem ipsum dummy text for the for the lorem ips<br>Lorem ipsum dummy text for the for the<br>Lorem ipsum dummy text for the for the lorem</div>
  <div class="abs btn-read">READ MORE</div>
  <div class="abs slide-arrow" style="left:51px"><svg width="14" height="20"><path d="M11 2 L3 10 L11 18" stroke="#fff" stroke-width="3.5" fill="none"/></svg></div>
  <div class="abs slide-arrow" style="left:962px"><svg width="14" height="20"><path d="M3 2 L11 10 L3 18" stroke="#fff" stroke-width="3.5" fill="none"/></svg></div>

  <div class="abs below-hero"></div>
  <div class="abs services"></div>
  <div class="abs services-tab">Our Services</div>
  <svg class="abs" style="left:122px;top:503px" width="12" height="18"><path d="M10 1 L2 9 L10 17" stroke="#444" stroke-width="3" fill="none"/></svg>
  <svg class="abs" style="left:907px;top:503px" width="12" height="18"><path d="M2 1 L10 9 L2 17" stroke="#444" stroke-width="3" fill="none"/></svg>
  <div class="abs service-sep" style="left:364px"></div>
  <div class="abs service-sep" style="left:560px"></div>
  <div class="abs service-sep" style="left:758px"></div>

  <div class="abs service" style="left:149px">
    <div class="service-icon"><svg width="28" height="28" viewBox="0 0 28 28"><circle cx="14" cy="14" r="9" fill="none" stroke="#980a52" stroke-width="4" stroke-dasharray="4 3"/><circle cx="14" cy="14" r="4" fill="#980a52"/></svg></div>
    IT Support &amp; Management
  </div>
  <div class="abs service" style="left:371px">
    <div class="service-icon"><svg width="30" height="24" viewBox="0 0 30 24"><path d="M8 20 C2 20 2 12 8 12 C8 5 18 4 20 10 C26 9 28 20 22 20 Z" fill="#980a52"/><path d="M15 10 L11 15 H13.5 V19 H16.5 V15 H19 Z" fill="#dcaa00"/></svg></div>
    Cloud Computing
  </div>
  <div class="abs service" style="left:568px">
    <div class="service-icon"><svg width="26" height="26" viewBox="0 0 26 26"><rect x="3" y="6" width="18" height="13" rx="1" fill="#980a52"/><rect x="10" y="19" width="4" height="4" fill="#980a52"/><rect x="7" y="22" width="10" height="2" fill="#980a52"/><path d="M19 2 L21 6 L24 4 L22 9 L18 8 Z" fill="#980a52"/></svg></div>
    Disaster Recovery
  </div>
  <div class="abs service" style="left:754px">
    <div class="service-icon"><svg width="24" height="24" viewBox="0 0 24 24"><rect x="3" y="3" width="11" height="11" fill="none" stroke="#980a52" stroke-width="3"/><rect x="10" y="10" width="11" height="11" fill="none" stroke="#980a52" stroke-width="3"/></svg></div>
    Virtualisation
  </div>

  <div class="abs welcome-mark"></div>
  <div class="abs welcome-title">Welcome to <span>plumbwick</span></div>
  <div class="abs dots"></div>
  <div class="abs about-text">
    <p>Plumbwick was established with a specific aim: to consistently deliver an advanced and comprehensive IT service for ambitious growing companies across many industry sectors. We aim to provide the very best in service and support, and to aid business growth through the effective and skilled use of modern IT solutions</p>
    <p>Founded in 2003, we have grown rapidly and have delivered successful business solutions to small and medium sized businesses, working with customers across a wide IT spectrum. The knowledge, experience and expertise.</p>
  </div>
  <div class="abs read-more">Read more »</div>

  <div class="abs video">
    <div class="video-frame" role="img" aria-label="Video still of a team joining hands in a circle, seen from below"></div>
    <div class="video-bar">
      <svg width="7" height="8"><path d="M0 0 L7 4 L0 8 Z" fill="#333"/></svg>
      <svg width="8" height="8"><path d="M0 3 H2 L5 0 V8 L2 5 H0 Z" fill="#333"/></svg>
      <span>0:00 / 0:47</span><div class="track"></div>
      <svg width="12" height="7"><rect width="12" height="7" rx="2" fill="#555"/></svg>
    </div>
  </div>

  <div class="abs rule"></div>
  <div class="abs news"></div>
  <div class="abs date"><div class="m">AUG</div><div class="d">12</div></div>
  <svg class="abs" style="left:176px;top:838px" width="16" height="44"><path d="M2 0 L14 22 L2 44" stroke="#ddd" stroke-width="2" fill="none"/></svg>
  <div class="abs news-text"><b>Duis aute irure dolor</b> in reprehenderit in voluptate velit esse cillum dolore eu fugiat nulla pariatur. Excepteur sint occaecat cupidatat non proident, sunt in culpa qui officia deserunt mollit anim lorem ipsum lorem ispm.</div>
  <div class="abs view-all">View All &gt;&gt;</div>

  <footer class="abs footer"></footer>
  <div class="abs foot-h" style="left:115px;top:930px">Quick Links</div>
  <div class="abs foot-link" style="left:113px;top:961px">HOME</div>
  <div class="abs foot-link" style="left:113px;top:993px">ABOUT US</div>
  <div class="abs foot-link" style="left:113px;top:1025px">WHAT WE DO</div>
  <div class="abs foot-link" style="left:113px;top:1057px">NEWS BLOG</div>
  <div class="abs foot-link" style="left:220px;top:961px">ARTICLES</div>
  <div class="abs foot-link" style="left:220px;top:993px">CLIENTS</div>
  <div class="abs foot-link" style="left:220px;top:1025px">PARTNERS</div>
  <div class="abs foot-link" style="left:220px;top:1057px">CONTACT US</div>
  <div class="abs divider" style="left:326px"></div>

  <div class="abs foot-h" style="left:350px;top:930px">Quick Contact</div>
  <div class="abs field" style="top:955px;height:23px">Name</div>
  <div class="abs field" style="top:985px;height:22px">Email</div>
  <div class="abs field" style="top:1014px;height:39px">Message</div>
  <div class="abs btn-gold" style="left:345px;top:1061px;width:59px;height:20px">Submit</div>
  <div class="abs divider" style="left:573px"></div>

  <div class="abs foot-h" style="left:595px;top:930px">Contact Info</div>
  <div class="abs info" style="top:962px">
    <svg width="10" height="14" viewBox="0 0 10 14"><path d="M5 0 C2 0 0 2 0 5 C0 8 5 14 5 14 C5 14 10 8 10 5 C10 2 8 0 5 0 Z" fill="#dcaa00"/><circle cx="5" cy="5" r="2" fill="#980a52"/></svg>
    <span>Lorem ipsum dolor sit<br>amet, consectetuer<br>adipiscing elit.</span>
  </div>
  <div class="abs info" style="top:1017px">
    <svg width="13" height="13" viewBox="0 0 13 13"><circle cx="6.5" cy="6.5" r="5.5" fill="none" stroke="#dcaa00" stroke-width="1.5"/><path d="M4.5 3.5 L6 5 L5 6 L7 8 L8 7 L9.5 8.5 L8.5 9.5 C6 9.5 3.5 7 3.5 4.5 Z" fill="#dcaa00"/></svg>
    <span>020 7946 0388</span>
  </div>
  <div class="abs info" style="top:1045px">
    <svg width="13" height="10" viewBox="0 0 13 10"><rect width="13" height="10" fill="#dcaa00"/><path d="M0 0 L6.5 5.5 L13 0" stroke="#980a52" fill="none"/></svg>
    <span>info@plumbwick.net</span>
  </div>
  <div class="abs divider" style="left:781px"></div>

  <div class="abs foot-h" style="left:117px;top:1114px">News Letter</div>
  <div class="abs" style="left:227px;top:1113px;width:211px;height:26px;background:#fff;border-radius:3px;font-size:11px;color:#999;padding:6px 12px">Enter e-mail</div>
  <div class="abs btn-gold" style="left:376px;top:1116px;width:60px;height:20px">Submit</div>
  <div class="abs foot-h" style="left:487px;top:1114px">Follow us</div>
  <div class="abs social" style="left:569px;background:#3b5a9a" role="img" aria-label="Social profile link"></div>
  <div class="abs social" style="left:606px;background:#3aa6e0" role="img" aria-label="Social profile link"></div>
  <div class="abs social" style="left:638px;background:#1a6fa8" role="img" aria-label="Social profile link"></div>

  <div class="abs copyright">© 2014 plumbwick. All Rights Reserved.</div>
</div>
</body>
</html>
```